OBK Farcoast Logistics Limited

We need the buissnes card to be very exclusive. As we are all young in our company. We need this to be the gate to make our clients feel deep interest for us.

We are focused in as International Trade advisors, and our products go from Oil Tanker Ships to Rubber balls for dogs.

Our Slogan is Bringing Far Near.
And our main marketing will be through Internet.

We were stablished in 2009 In Mexico and we also have offices in Hong Kong.
We have representatives in China and Europe.

Target Market(s)

Is every company or Individual that wants to develop an International Project or product development or Logistic service of Goods and people.
Some of our current projects are Ship Brokerage, Mine Brokerage, Real State and Product Pormotional development.

Industry/Entity Type

It Company

Requirements
Must have
• Our Logo and slogan, and make the card accoriding to the logo.
Nice to have
• Our Colors

```html
<!DOCTYPE html>
<html lang="en">
<head>
<meta charset="utf-8">
<title>OBK Farcoast Logistics Limited — Business Card</title>
<link rel="stylesheet" href="https://fonts.googleapis.com/css2?family=Open+Sans:wght@300;400;600;700&display=swap">
<style>
  :root {
    --bg: #ecebe8;
    --card: #ffffff;
    --green: #8cc63f;
    --blue: #29a0dc;
    --navy: #2f3f96;
    --text: #555a60;
    --edge: #d9d9d9;
  }
  html, body {
    margin: 0;
    padding: 0;
    overflow: hidden;
    background: var(--bg);
  }
  .canvas {
    position: relative;
    width: 1200px;
    height: 720px;
    overflow: hidden;
    background: var(--bg);
    font-family: "Open Sans", Arial, sans-serif;
  }
  .card {
    position: absolute;
    top: 205px;
    width: 540px;
    height: 309px;
    background: var(--card);
    box-shadow: 0 1px 3px rgba(0,0,0,.12), 0 0 0 1px var(--edge);
  }
  .card--front { left: 40px; }
  .card--back  { left: 620px; }

  .mark-circle {
    position: absolute;
    border-radius: 50%;
    background: var(--blue);
  }
  .card--front .mark-circle { left: 50px; top: 60px; width: 200px; height: 200px; }
  .card--back  .mark-circle { left: 120px; top: 38px; width: 160px; height: 160px; }

  .brand-name {
    position: absolute;
    margin: 0;
    color: var(--green);
    font-weight: 600;
    line-height: 1;
    letter-spacing: 2px;
  }
  .brand-slogan {
    position: absolute;
    margin: 0;
    color: var(--blue);
    font-weight: 400;
    line-height: 1;
    white-space: nowrap;
  }
  .card--front .brand-name   { left: 318px; top: 14px; font-size: 58px; }
  .card--front .brand-slogan { left: 320px; top: 74px; font-size: 13px; }
  .card--back  .brand-name   { left: 160px; top: 208px; font-size: 66px; }
  .card--back  .brand-slogan { left: 163px; top: 276px; font-size: 14px; }

  .person {
    position: absolute;
    left: 320px;
    top: 102px;
  }
  .person-name {
    margin: 0;
    color: var(--green);
    font-size: 17px;
    font-weight: 700;
    line-height: 1.2;
  }
  .person-role {
    margin: 0;
    color: var(--blue);
    font-size: 12px;
    font-weight: 600;
  }
  .contact-list {
    list-style: none;
    margin: 8px 0 0;
    padding: 0;
    color: var(--text);
    font-size: 12.5px;
  }
  .contact-item {
    display: flex;
    align-items: center;
    gap: 7px;
    height: 19px;
  }
  .contact-icon {
    width: 12px;
    height: 12px;
    flex: none;
  }
  .contact-address {
    margin: 10px 0 0;
    color: var(--text);
    font-size: 12.5px;
    line-height: 1.5;
  }

  .web-address {
    position: absolute;
    left: 345px;
    top: 98px;
    margin: 0;
    color: var(--text);
    font-size: 14px;
    letter-spacing: 3px;
  }
  .web-address .domain { color: var(--blue); }
</style>
</head>
<body>
<main class="canvas">

  <section class="card card--front" aria-label="Business card front">
    <div class="mark-circle" aria-hidden="true"></div>
    <h1 class="brand-name">OBK</h1>
    <p class="brand-slogan">Bringing Far Near</p>

    <div class="person">
      <p class="person-name">Your Name</p>
      <p class="person-role">Position</p>
      <ul class="contact-list">
        <li class="contact-item">
          <svg class="contact-icon" viewBox="0 0 12 12" aria-hidden="true"><circle cx="6" cy="6" r="6" fill="var(--navy)"/><path d="M4 3.2 5 4.6 4.5 5.3c.5 1 1.2 1.7 2.2 2.2l.7-.5 1.4 1-.6 1C6 8.8 3.2 6 3 3.8Z" fill="#fff"/></svg>
          <span>123-456-7890</span>
        </li>
        <li class="contact-item">
          <svg class="contact-icon" viewBox="0 0 12 12" aria-hidden="true"><circle cx="6" cy="6" r="6" fill="var(--navy)"/><rect x="4" y="2.5" width="4" height="7" rx=".8" fill="#fff"/><rect x="4.7" y="3.4" width="2.6" height="4.2" fill="var(--navy)"/></svg>
          <span>123-456-7890</span>
        </li>
        <li class="contact-item">
          <svg class="contact-icon" viewBox="0 0 12 12" aria-hidden="true"><circle cx="6" cy="6" r="6" fill="var(--navy)"/><rect x="3" y="4" width="6" height="4.2" fill="#fff"/><path d="M3 4 6 6.4 9 4" fill="none" stroke="var(--navy)" stroke-width=".7"/></svg>
          <span>info@farcoast.com</span>
        </li>
        <li class="contact-item">
          <svg class="contact-icon" viewBox="0 0 12 12" aria-hidden="true"><circle cx="6" cy="6" r="6" fill="var(--navy)"/><circle cx="6" cy="6" r="3.3" fill="none" stroke="#fff" stroke-width=".8"/><path d="M2.7 6h6.6M6 2.7v6.6" stroke="#fff" stroke-width=".7"/></svg>
          <span>www.farcoast.com</span>
        </li>
      </ul>
      <p class="contact-address">00, Complex Name<br>street, city 000452</p>
    </div>
  </section>

  <section class="card card--back" aria-label="Business card back">
    <div class="mark-circle" aria-hidden="true"></div>
    <p class="web-address">www.<span class="domain">farcoast</span>.com</p>
    <h2 class="brand-name">OBK</h2>
    <p class="brand-slogan">Bringing Far Near</p>
  </section>

</main>
</body>
</html>
```